Brightway Haus Inc. Business Card Design

Brightway Haus Inc. is in search of a great clean design for our business cards!

Looking to incorporate our full logo and watermark on side one (however, I am open to having the text and watermark separated within the design.)

On side two, I am looking to have contact information (Name, Position, Phone #, Email, Website (www.thebrightwayhaus.ca). Can have the logo and/or watermark as part of the design if applicable.

Please add tagline "Where Shine Counts" on either side 1 or 2. This tagline can be in a sans serif, serif or cursive font as long as it compliments overall design. Capitalization can be title or sentence case depending on how it fits within the design.

Get creative!! Looking for a clean, crisp, premium design! Looking for a glossy card finish with spot UV features when printed. Cards will also be printed with rounded corners. Standard dimensions (3.5 x 2).

Target Market(s)

B2B - primary clients are business owners or property management corporations. (residential jobs are few and far between)

Industry/Entity Type

Business

Contact Information for Business Card

- clean, crisp design
- double sided
- spot UV accents and glossy finish upon printing
- standard business card size (3.5 x 2) with rounded corners
- please see project description for requirements per side

Font styles to use
Sans Serif

Requirements
Must have
• - adequate bleeds with print ready files
• - cohesive design elements between side 1 & 2
• - spot UV elements (can be on both sides or just one, use your discretion)
• - colour pallet should match the logo file provided
• - incorporate tagline "where shine counts" (this tagline can be in a serif or sans serif font as long as it is complimentary to the overall design.
Nice to have
• - Premium elements with a clean design
Should not have
• - Please omit cartoon or whimsical like designs, think premium.
• - Colours should not stray from the pallet of the provided logo.

```html
<!DOCTYPE html>
<html lang="en">
<head>
<meta charset="utf-8">
<title>Brightway Haus Inc. Business Card</title>
<link href="https://fonts.googleapis.com/css2?family=Source+Sans+3:wght@400;600;700&display=swap" rel="stylesheet">
<style>
  :root {
    --teal: #12b8bd;
    --navy: #1c2554;
    --grey: #b3b3b3;
    --text: #555a60;
    --card: #ffffff;
    --card-back: #f2f2f2;
    --stage: #2b2b2b;
  }
  * { margin: 0; padding: 0; box-sizing: border-box; }
  html, body { width: 1200px; height: 960px; overflow: hidden; }
  body {
    background: var(--stage);
    font-family: "Source Sans 3", Arial, sans-serif;
    position: relative;
  }
  .card {
    position: absolute;
    width: 600px;
    height: 343px;
    border-radius: 22px;
    overflow: hidden;
  }
  .card-front { left: 314px; top: 113px; background: var(--card); }
  .card-back { left: 311px; top: 472px; background: var(--card-back); }

  .brand-name {
    color: var(--navy);
    font-weight: 700;
    white-space: nowrap;
    display: flex;
    align-items: center;
  }
  .brand-square {
    display: inline-block;
    background: var(--teal);
  }
  .card-front .brand-name { position: absolute; left: 32px; top: 36px; font-size: 20px; z-index: 1; }
  .card-front .brand-square { width: 18px; height: 18px; margin-right: 9px; }

  .watermark-panel {
    position: absolute;
    left: 272px; top: 0;
    width: 328px; height: 343px;
    background: linear-gradient(160deg, var(--teal) 0%, var(--teal) 45%, var(--navy) 100%);
    clip-path: polygon(46px 0, 100% 0, 100% 100%, 0 100%);
  }

  .person { position: absolute; left: 32px; top: 114px; }
  .person-name { color: var(--teal); font-weight: 700; font-size: 17px; line-height: 22px; }
  .person-role { color: var(--navy); font-size: 17px; line-height: 22px; }

  .address { position: absolute; left: 32px; top: 170px; color: var(--text); font-size: 15.5px; line-height: 19px; }

  .contacts { position: absolute; left: 32px; top: 215px; list-style: none; }
  .contacts li {
    display: flex; align-items: center;
    color: var(--text); font-size: 15.5px; line-height: 19px;
  }
  .contacts svg { width: 13px; height: 13px; margin-right: 10px; fill: var(--teal); }

  .card-back .brand-name {
    position: absolute; left: 0; right: 0; top: 136px;
    justify-content: center;
    font-size: 40px;
  }
  .card-back .brand-square { width: 32px; height: 32px; margin-right: 14px; }

  .tagline {
    position: absolute; left: 100px; right: 100px; top: 276px;
    display: flex; align-items: center; justify-content: center;
    color: var(--navy); font-weight: 600; font-size: 19px;
    white-space: nowrap;
  }
  .tagline .accent { color: var(--teal); }
  .tagline-rule { flex: 1; height: 1px; }
  .tagline-rule.left { background: linear-gradient(90deg, transparent, var(--navy)); margin-right: 2px; }
  .tagline-rule.right { background: linear-gradient(90deg, var(--navy), transparent); margin-left: 2px; }
</style>
</head>
<body>

<section class="card card-front">
  <div class="watermark-panel" role="img" aria-label="Large brand watermark in teal, navy and grey"></div>
  <div class="brand-name"><span class="brand-square"></span>BRIGHTWAY HAUS INC.</div>

  <div class="person">
    <p class="person-name">MARA ELLISON</p>
    <p class="person-role">CEO/FOUNDER</p>
  </div>

  <p class="address">4120 Harbourview Road<br>Halifax, Nova Scotia B3H 2Y9</p>

  <ul class="contacts">
    <li><svg viewBox="0 0 16 16"><path d="M2 5c0-2 3-3 6-3s6 1 6 3v1h-3V5H5v1H2z M3 8h10l1 6H2z"/></svg>902 418 7730</li>
    <li><svg viewBox="0 0 16 16"><path d="M4 1h8v14H4z M5.5 3v9h5V3z"/></svg>902 555 6142</li>
    <li><svg viewBox="0 0 16 16"><path d="M4 2h8v4H4z M1 7h14v6h-3v2H4v-2H1z M5 11v3h6v-3z"/></svg>902 418 7731</li>
    <li><svg viewBox="0 0 16 16"><path d="M1 4h14v1l-7 4-7-4z M1 6.5l7 4 7-4V12H1z"/></svg>info@brightwayhaus.ca</li>
    <li><svg viewBox="0 0 16 16"><circle cx="8" cy="8" r="7"/></svg>www.thebrightwayhaus.ca</li>
  </ul>
</section>

<section class="card card-back">
  <div class="brand-name"><span class="brand-square"></span>BRIGHTWAY HAUS INC.</div>
  <p class="tagline">
    <span class="tagline-rule left"></span>
    <span>Where <span class="accent">Shine</span> Counts</span>
    <span class="tagline-rule right"></span>
  </p>
</section>

</body>
</html>
```